Road Construction Company needs business cards

We would like a new business card designed for our business.

We're a road construction company based in Qld, Australia.

Can the business card please have the following information on it.

Name: Warren Halbeck
Position: General Manager
Phone: 0472 915 348
Email: Warren.halbeck@tovrin.com.au
Address: 87 Marrow Ave, Pendlebay, QLD, 4023
Website: www.tovrin.com.au

Visually we'd like the card to be professional and simple.

Attached is our logo.

Our website is www.tovrin.com.au

Target Market(s)

Men aged 25-60

Contact Information for Business Card

As listed in project description

Font styles to use
Serif

Requirements
Must have
• Large logo on back of card

```html
<!DOCTYPE html>
<html lang="en">
<head>
<meta charset="utf-8">
<title>Tovrin Road Construction – Business Card</title>
<link href="https://fonts.googleapis.com/css2?family=Noto+Serif:wght@400;700&display=swap" rel="stylesheet">
<style>
  :root {
    --backdrop: #4a4a4a;
    --card: #161616;
    --brand-blue: #0a56a6;
    --accent-blue: #34a5dc;
    --ink-light: #f2f2f2;
  }
  * { margin: 0; padding: 0; box-sizing: border-box; }
  html, body {
    width: 1200px; height: 801px; overflow: hidden;
    background: var(--backdrop);
    font-family: "Noto Serif", Georgia, serif;
  }
  .sheet {
    position: relative; width: 1200px; height: 801px;
    display: flex; justify-content: center; align-items: center; gap: 30px;
  }
  .card {
    position: relative; width: 540px; height: 309px;
    background: var(--card);
    border-radius: 14px;
    border-bottom: 3px solid var(--accent-blue);
    overflow: hidden;
    box-shadow: 0 10px 24px rgba(0,0,0,.35);
  }
  .wordmark {
    position: absolute; color: var(--brand-blue);
    font-weight: 700; line-height: 1; white-space: nowrap;
  }
  .card--front .wordmark { left: 42px; top: 40px; font-size: 30px; }
  .card--back .wordmark {
    left: 0; right: 0; top: 50%; transform: translateY(-50%);
    text-align: center; font-size: 40px;
  }
  .address {
    position: absolute; right: 34px; top: 92px;
    color: var(--ink-light); font-size: 14px; line-height: 1.5; text-align: left;
  }
  .edge-tab {
    position: absolute; left: 0; top: 168px; width: 28px; height: 30px;
    background: var(--accent-blue);
  }
  .person { position: absolute; left: 44px; top: 148px; }
  .person__name { color: var(--accent-blue); font-size: 25px; font-weight: 700; line-height: 1.1; }
  .person__role { color: var(--ink-light); font-size: 15px; margin-top: 4px; }
  .divider {
    position: absolute; left: 44px; right: 34px; top: 212px;
    height: 1px; background: var(--accent-blue);
  }
  .contacts {
    position: absolute; left: 44px; top: 222px; list-style: none;
    color: var(--ink-light); font-size: 13.5px; line-height: 1.6;
  }
  .contacts li { display: flex; align-items: center; gap: 8px; }
  .contacts svg { width: 12px; height: 12px; fill: var(--accent-blue); flex: none; }
</style>
</head>
<body>
<main class="sheet">
  <section class="card card--front" aria-label="Card front">
    <div class="wordmark">Tovrin Road Construction</div>
    <p class="address">87 Marrow Ave,<br>Pendlebay, QLD, 4023</p>
    <span class="edge-tab"></span>
    <div class="person">
      <h1 class="person__name">Warren Halbeck</h1>
      <p class="person__role">General Manager</p>
    </div>
    <span class="divider"></span>
    <ul class="contacts">
      <li>
        <svg viewBox="0 0 24 24" aria-hidden="true"><path d="M6.6 10.8a15 15 0 0 0 6.6 6.6l2.2-2.2a1 1 0 0 1 1-.25 11.4 11.4 0 0 0 3.6.57 1 1 0 0 1 1 1V20a1 1 0 0 1-1 1A17 17 0 0 1 3 4a1 1 0 0 1 1-1h3.5a1 1 0 0 1 1 1c0 1.25.2 2.45.57 3.6a1 1 0 0 1-.25 1z"/></svg>
        0472 915 348
      </li>
      <li>
        <svg viewBox="0 0 24 24" aria-hidden="true"><path d="M2 5h20v14H2zm2 2v.5l8 5 8-5V7z"/></svg>
        Warren.halbeck@tovrin.com.au
      </li>
      <li>
        <svg viewBox="0 0 24 24" aria-hidden="true"><circle cx="12" cy="12" r="10"/></svg>
        www.tovrin.com.au
      </li>
    </ul>
  </section>

  <section class="card card--back" aria-label="Card back">
    <div class="wordmark">Tovrin Road Construction</div>
  </section>
</main>
</body>
</html>
```